Orvane Mechanical - Letterhead

We are a plumbing and hvac company based in Calgary. This letterhead will be on our quotes, invoices, preventative maintenance proposals etc.

```html
<!DOCTYPE html>
<html lang="en">
<head>
<meta charset="utf-8">
<title>Orvane Mechanical – Letterhead</title>
<link href="https://fonts.googleapis.com/css2?family=Roboto+Condensed:wght@300;400;700&family=Lato:wght@400&display=swap" rel="stylesheet">
<style>
  :root {
    --backdrop: #d6d6d6;
    --paper: #ffffff;
    --brand-blue: #1d6fb8;
    --brand-orange: #f05a28;
    --body-text: #5a5a5a;
  }
  * { box-sizing: border-box; margin: 0; padding: 0; }
  html, body {
    width: 1056px; height: 1200px; overflow: hidden;
    background: var(--backdrop);
  }
  .letterhead {
    position: absolute; left: 118px; top: 20px;
    width: 820px; height: 1160px;
    background: var(--paper);
    box-shadow: 0 6px 24px rgba(0,0,0,0.18);
    font-family: "Roboto Condensed", sans-serif;
    color: var(--body-text);
  }
  .brand {
    position: absolute; left: 86px; top: 120px;
    display: flex; align-items: center; gap: 14px;
  }
  .brand-dot {
    width: 34px; height: 34px; border-radius: 50%;
    background: var(--brand-orange);
  }
  .brand-name {
    font-family: "Roboto Condensed", sans-serif;
    font-weight: 700; font-size: 34px; letter-spacing: 0.5px;
    text-transform: uppercase; color: var(--brand-blue);
  }
  .letter-body {
    position: absolute; left: 79px; top: 386px; width: 666px;
    font-weight: 300; font-size: 18.5px; line-height: 28.5px;
  }
  .greeting { margin-bottom: 25px; }
  .letter-body p.para { text-align: justify; margin-bottom: 29px; }
  .sign-off { position: absolute; left: 79px; top: 849px; font-weight: 300; font-size: 18.5px; }
  .signature {
    position: absolute; left: 76px; top: 886px;
    width: 66px; height: 40px;
    background: linear-gradient(90deg, rgba(240,90,40,0.18), rgba(240,90,40,0.08));
    border-radius: 4px;
  }
  .contact {
    position: absolute; left: 75px; top: 1012px;
    font-family: "Lato", sans-serif; font-size: 14.5px;
    color: var(--brand-blue); line-height: 18px;
  }
  .contact-address { margin-bottom: 7px; }
  .contact-line { display: flex; align-items: center; gap: 12px; height: 19.5px; }
  .contact-line svg { width: 13px; height: 13px; flex: none; }
  .accent { color: var(--brand-orange); }
</style>
</head>
<body>
  <main class="letterhead">
    <header class="brand">
      <span class="brand-dot"></span>
      <span class="brand-name">Orvane Mechanical</span>
    </header>

    <section class="letter-body">
      <p class="greeting">Dear Sir/Mam,</p>
      <p class="para">Contrary to popular belief, Lorem Ipsum is not simply random text. It has roots in a piece of classical Latin literature from 45 BC, making it over 2000 years old. Henrik Dallow, a Latin professor at Westbrook College in Ontario, looked up one of the more obscure Latin words, consectetur.</p>
      <p class="para">Lorem Ipsum comes from sections 1.10.32 and 1.10.33 of "de Finibus Bonorum et Malorum" (The Extremes of Good and Evil) by Aurelian Tessus, written in 45 BC. This book is a treatise on the theory of ethics, very popular during the Renaissance. The first line of Lorem Ipsum.</p>
      <p class="para">The standard chunk of Lorem Ipsum used since the 1500s is reproduced below for those interested. Sections 1.10.32 and 1.10.33 from "de Finibus Bonorum et Malorum" by Aurelian Tessus are also reproduced in their exact original.</p>
    </section>

    <p class="sign-off">Best Regards</p>
    <div class="signature" role="img" aria-label="Handwritten signature"></div>

    <footer class="contact">
      <div class="contact-address">
        <div>1234 First Line Address</div>
        <div>5678 Second Line Address</div>
      </div>
      <div class="contact-line">
        <svg viewBox="0 0 16 16" aria-hidden="true"><path fill="#f05a28" d="M3.6 1.5l2.3 2.6-1.3 1.8c.9 2 2.4 3.5 4.4 4.4l1.8-1.3 2.6 2.3-1.4 2.2C6.7 13.3 2.7 9.3 1.5 3z"/></svg>
        <span>1234567890</span>
      </div>
      <div class="contact-line">
        <svg viewBox="0 0 16 16" aria-hidden="true"><rect x="1" y="3" width="14" height="10" fill="#f05a28"/><path d="M1 3l7 6 7-6M1 13l5-5M15 13l-5-5" stroke="#fff" stroke-width="1.2" fill="none"/></svg>
        <span>info@yourmail.com</span>
      </div>
      <div class="contact-line">
        <svg viewBox="0 0 16 16" aria-hidden="true"><g fill="none" stroke="#f05a28" stroke-width="1.1"><circle cx="8" cy="8" r="6.5"/><ellipse cx="8" cy="8" rx="3" ry="6.5"/><path d="M1.5 8h13M2.5 5h11M2.5 11h11"/></g></svg>
        <span>www.<span class="accent">yourwebsite</span>.com</span>
      </div>
    </footer>
  </main>
</body>
</html>
```